TALMORK

The business want a professional looking business card. We have a scetch we will add but want the extra upgrade, and would like more suggestions for variations of our business cards.

```html
<!DOCTYPE html>
<html lang="en">
<head>
<meta charset="utf-8">
<title>Talmork Business Cards</title>
<link href="https://fonts.googleapis.com/css2?family=Cormorant+Garamond:wght@500;600&family=Poppins:wght@400&display=swap" rel="stylesheet">
<style>
  :root {
    --backdrop: #2b2b2d;
    --card: #222223;
    --gold: #cfa64c;
    --gold-soft: #b8913f;
    --mark-dark: #171718;
  }
  * { margin: 0; padding: 0; box-sizing: border-box; }
  html, body { width: 1200px; height: 900px; overflow: hidden; }
  body { background: var(--backdrop); position: relative; font-family: "Poppins", sans-serif; }

  .card {
    position: absolute;
    width: 630px;
    height: 360px;
    background: var(--card);
    border-radius: 22px;
    box-shadow: 0 14px 30px rgba(0,0,0,0.45);
    overflow: hidden;
  }
  .card--back { left: 500px; top: 70px; }
  .card--front { left: 70px; top: 470px; }

  .wordmark {
    font-family: "Cormorant Garamond", serif;
    font-weight: 600;
    color: var(--gold);
    letter-spacing: 0.28em;
    line-height: 1;
  }
  .tagline {
    font-family: "Poppins", sans-serif;
    color: var(--gold);
    letter-spacing: 0.3em;
    font-size: 12px;
    margin-top: 8px;
  }

  .card--back .brand { position: absolute; right: 46px; bottom: 50px; text-align: right; }
  .card--back .wordmark { font-size: 40px; }
  .card--back .emblem {
    position: absolute; left: 120px; top: 40px;
    width: 230px; height: 230px; border-radius: 50%;
    background: var(--mark-dark);
  }

  .card--front .brand { position: absolute; left: 44px; top: 40px; }
  .card--front .wordmark { font-size: 46px; }
  .card--front .tagline { margin-left: 70px; }
  .card--front .emblem {
    position: absolute; right: 80px; bottom: 60px;
    width: 150px; height: 150px; border-radius: 50%;
    background: var(--gold);
  }

  .contact { position: absolute; left: 44px; top: 170px; color: var(--gold); }
  .contact__name { font-family: "Cormorant Garamond", serif; font-weight: 600; font-size: 28px; }
  .contact__role, .contact__person { font-size: 14px; line-height: 1.45; }
  .contact__list { list-style: none; margin-top: 12px; font-size: 14px; }
  .contact__list li { display: flex; align-items: center; gap: 8px; line-height: 1.6; }
  .contact__list svg { width: 12px; height: 12px; fill: var(--gold); flex: none; }
</style>
</head>
<body>

<section class="card card--back">
  <div class="emblem" aria-hidden="true"></div>
  <div class="brand">
    <div class="wordmark">TALMORK</div>
    <div class="tagline">SINCE 2026</div>
  </div>
</section>

<section class="card card--front">
  <div class="brand">
    <div class="wordmark">TALMORK</div>
    <div class="tagline">SINCE 2026</div>
  </div>
  <div class="contact">
    <div class="contact__name">Talmork Vestbakk</div>
    <div class="contact__role">CEO &amp; Founder</div>
    <div class="contact__person">Aksel Rune Halvorsen</div>
    <ul class="contact__list">
      <li><svg viewBox="0 0 12 12"><path d="M2 1h3l1 3-1.5 1a6 6 0 0 0 2.5 2.5L8 6l3 1v3c0 .6-.4 1-1 1A10 10 0 0 1 1 2c0-.6.4-1 1-1z"/></svg>004791234567</li>
      <li><svg viewBox="0 0 12 12"><path d="M1 2h10v1L6 6.5 1 3z M1 4.2l5 3.5 5-3.5V10H1z"/></svg>talmork.llc@mailbox.com</li>
      <li><svg viewBox="0 0 12 12"><circle cx="6" cy="6" r="5" fill="none" stroke="#cfa64c" stroke-width="1.2"/><path d="M1 6h10M6 1c-2 2.5-2 7.5 0 10M6 1c2 2.5 2 7.5 0 10" fill="none" stroke="#cfa64c" stroke-width="1"/></svg>www.talmork.llc</li>
    </ul>
  </div>
  <div class="emblem" aria-hidden="true"></div>
</section>

</body>
</html>
```